Keystone Trench Co Business Card*

Looking for a professional, clean and crisp business card

I am in the underground utilities industry and am just looking for a really impressive business card. I would like our card to be white with our symbol crisp and clear with it protruding. I also have a business partner that will require his name and info on the card once the design is set. I would like to have our website info on the card which is;
http://keystonetrenchco.example/

Contact Information for Business Card

Website, contact name, number and email

```html
<!DOCTYPE html>
<html lang="en">
<head>
<meta charset="utf-8">
<title>Keystone Trench Co Business Card</title>
<link href="https://fonts.googleapis.com/css2?family=Oswald:wght@500&family=Poppins:wght@400&display=swap" rel="stylesheet">
<style>
  :root {
    --backdrop: #c9cccf;
    --card: #f4f4f2;
    --edge: #15207a;
    --brand-blue: #3b5eae;
    --accent-red: #e8303a;
    --ink-grey: #6d6d6d;
    --icon-blue: #4a6ab5;
  }
  * { margin: 0; padding: 0; box-sizing: border-box; }
  html, body { width: 1200px; height: 824px; overflow: hidden; }
  body {
    background: var(--backdrop);
    font-family: "Poppins", sans-serif;
    position: relative;
  }
  .card {
    position: absolute;
    top: 263px;
    width: 520px;
    height: 298px;
    background: var(--card);
    border-bottom: 5px solid var(--edge);
    box-shadow: 0 6px 18px rgba(0,0,0,0.18);
  }
  .card--front { left: 53px; }
  .card--back { left: 627px; }

  .holder {
    position: absolute;
    top: 92px;
    right: 58px;
    text-align: right;
  }
  .holder__name {
    font-family: "Oswald", sans-serif;
    font-weight: 500;
    font-size: 31px;
    letter-spacing: 0.5px;
    color: var(--brand-blue);
    line-height: 1.1;
  }
  .holder__role {
    font-size: 19px;
    color: var(--accent-red);
    line-height: 1.1;
  }

  .contact {
    position: absolute;
    left: 40px;
    bottom: 40px;
    font-size: 14px;
    line-height: 1.45;
    color: var(--ink-grey);
    list-style: none;
  }
  .contact__address { padding-left: 22px; margin-bottom: 2px; }
  .contact__item { display: flex; align-items: center; gap: 8px; }
  .contact__icon { width: 14px; height: 14px; fill: var(--icon-blue); flex: none; }

  .brand {
    position: absolute;
    inset: 0;
    display: flex;
    align-items: center;
    justify-content: center;
    gap: 14px;
  }
  .brand__dot {
    width: 30px;
    height: 30px;
    border-radius: 50%;
    background: var(--edge);
  }
  .brand__name {
    font-family: "Oswald", sans-serif;
    font-weight: 500;
    font-size: 34px;
    letter-spacing: 1px;
    color: var(--edge);
    text-transform: uppercase;
  }
</style>
</head>
<body>
  <section class="card card--front">
    <div class="holder">
      <div class="holder__name">DANIEL HARROW</div>
      <div class="holder__role">President</div>
    </div>
    <ul class="contact">
      <li class="contact__address">4120 Birchwood Road<br>Fairbanks, Alaska 99701</li>
      <li class="contact__item">
        <svg class="contact__icon" viewBox="0 0 24 24"><path d="M6.6 10.8a15.1 15.1 0 0 0 6.6 6.6l2.2-2.2c.3-.3.7-.4 1-.2 1.1.4 2.3.6 3.6.6.6 0 1 .4 1 1V20c0 .6-.4 1-1 1A17 17 0 0 1 3 4c0-.6.4-1 1-1h3.5c.6 0 1 .4 1 1 0 1.3.2 2.5.6 3.6.1.3 0 .7-.2 1z"/></svg>
        <span>555-014-2387</span>
      </li>
      <li class="contact__item">
        <svg class="contact__icon" viewBox="0 0 24 24"><path d="M3 5h18v14H3z M3 5l9 7 9-7" fill="none" stroke="currentColor"/><path d="M2 4h20v16H2zm2 2v.5l8 6 8-6V6zm0 3v9h16V9l-8 6z"/></svg>
        <span>info@keystonetrenchco.example</span>
      </li>
      <li class="contact__item">
        <svg class="contact__icon" viewBox="0 0 24 24"><circle cx="12" cy="12" r="10"/><path d="M2 12h20M12 2c3 3 3 17 0 20M12 2c-3 3-3 17 0 20" fill="none" stroke="#fff" stroke-width="1.4"/></svg>
        <span>www.keystonetrenchco.example</span>
      </li>
    </ul>
  </section>

  <section class="card card--back">
    <div class="brand">
      <span class="brand__dot"></span>
      <span class="brand__name">Keystone Trench Co</span>
    </div>
  </section>
</body>
</html>
```